Heron Loan Partners Business Card

We need a business card design for our mortgage servicing company. In addition to servicing the loans of homeowners, we help homeowners with purchasing their homes and any mortgage refinancing. We would like to see designs that use the colors in the logo attached below (gold-ish yellow and navy blue), and any other design you deem fit! The design should communicate a simpler life with smart mortgages provided by Heron.

```html
<!DOCTYPE html>
<html lang="en">
<head>
<meta charset="utf-8">
<title>Heron Loan Partners Business Card</title>
<link rel="stylesheet" href="https://fonts.googleapis.com/css2?family=Open+Sans:wght@400;700&display=swap">
<style>
  :root {
    --backdrop: #2b2b2b;
    --card: #171717;
    --gold: #e3b13b;
    --navy: #231e4f;
    --white: #f4f4f4;
  }
  * { margin: 0; padding: 0; box-sizing: border-box; }
  html, body {
    width: 1200px; height: 689px; overflow: hidden;
    background: var(--backdrop);
    font-family: "Open Sans", Arial, sans-serif;
  }
  .stage {
    position: relative; width: 1200px; height: 689px;
    display: flex; align-items: center; justify-content: center; gap: 60px;
  }
  .card {
    position: relative; width: 520px; height: 297px;
    background: var(--card); border-radius: 22px;
    box-shadow: 0 14px 30px rgba(0,0,0,.45);
    overflow: hidden;
  }
  .brand {
    display: flex; align-items: center; gap: 14px;
    color: var(--gold); font-weight: 700;
  }
  .brand-dot { width: 14px; height: 14px; border-radius: 50%; background: var(--navy); }
  .card-front .brand {
    position: absolute; inset: 0; justify-content: center;
    font-size: 72px; letter-spacing: 1px;
  }
  .card-front .brand-dot { width: 22px; height: 22px; }
  .card-back .brand {
    position: absolute; left: 40px; top: 46px; font-size: 46px;
  }
  .holder { position: absolute; left: 40px; top: 138px; }
  .holder-name { color: var(--gold); font-weight: 700; font-size: 21px; letter-spacing: .5px; line-height: 1.1; }
  .holder-title { color: var(--white); font-size: 15px; margin-top: 2px; }
  .divider { position: absolute; left: 40px; right: 30px; top: 196px; height: 2px; background: var(--gold); }
  .address {
    position: absolute; right: 34px; top: 140px; text-align: right;
    color: var(--white); font-size: 13.5px; line-height: 1.35;
  }
  .contacts { position: absolute; left: 40px; top: 210px; list-style: none; }
  .contacts li {
    display: flex; align-items: center; gap: 9px;
    color: var(--white); font-size: 14.5px; line-height: 21px;
  }
  .contacts svg { width: 13px; height: 13px; fill: var(--gold); flex: none; }
</style>
</head>
<body>
<main class="stage">
  <section class="card card-front" aria-label="Card front">
    <div class="brand"><span class="brand-dot"></span><span>Heron</span></div>
  </section>

  <section class="card card-back" aria-label="Card back">
    <div class="brand"><span class="brand-dot"></span><span>Heron</span></div>

    <div class="holder">
      <p class="holder-name">DANA WHITFIELD</p>
      <p class="holder-title">Managing Director</p>
    </div>

    <p class="address">48 Harbor Lane, Easton<br>MD, 21601</p>

    <div class="divider"></div>

    <ul class="contacts">
      <li>
        <svg viewBox="0 0 24 24"><path d="M6.6 10.8a15.1 15.1 0 0 0 6.6 6.6l2.2-2.2c.3-.3.7-.4 1-.2 1.1.4 2.3.6 3.6.6.6 0 1 .4 1 1V20c0 .6-.4 1-1 1A17 17 0 0 1 3 4c0-.6.4-1 1-1h3.5c.6 0 1 .4 1 1 0 1.3.2 2.5.6 3.6.1.3 0 .7-.2 1z"/></svg>
        555 014 2290
      </li>
      <li>
        <svg viewBox="0 0 24 24"><path d="M2 5h20v14H2zM4 7v.5l8 5 8-5V7l-8 5z"/></svg>
        hello@heronloanpartners.com
      </li>
      <li>
        <svg viewBox="0 0 24 24"><circle cx="12" cy="12" r="10"/></svg>
        www.heronloanpartners.com
      </li>
    </ul>
  </section>
</main>
</body>
</html>
```